Create a book cover for brimvale QTR

We are looking for a designer to design a cover for a log book in two versions. The two versions only have a slight difference in page count and text, other than that, it is one design.

The main color is blue. No black, no white except book title and other text. The cover must closely relate to the interior pages provided in the attachment. The style should be simple and modern, no old school graphics and fonts. Apply color psychology in the design. Please be creative and you are allowed to use download templates and graphic elements, but you must provide commercial licenses.

Here are the basic information of the book:
1. Book title: MOTOR UPKEEP TRACKING JOURNAL
2. Book size: 6x9 inches
3. Page count: 61 (version 1) and 73 (version 2)
4. Platform: brimvale qtr

Requirement for version 1:
1. Front cover: book title
2. Spine: no book title and author name
3. Back cover: text on the top and pen name logo on the bottom middle
4. Back cover text:
• Your essential tool for tracking vehicle health and maintenance
• Dedicated sections for maintenance schedules and repair history
• Track up to 30 maintenance schedules and repair history
• Easy-to-use tables and clear layouts
• Perfect for all car owners, from enthusiasts to everyday drivers

We hope it helps you keep your vehicle in excellent condition. Please take a moment to leave a positive review on Brimvale and share your experience if you find it helpful. Thank you!

Requirement for version 2:
1. Front cover: book title ,text "COLOR PAGES"
4. Back cover text:
• Track up to 36 maintenance schedules and repair history

Export:
1. Cover design in PDF and editable file format.
2. Sources/Commercial licenses for everything you did not create by yourself including fonts.

```html
<!DOCTYPE html>
<html lang="en">
<head>
<meta charset="utf-8">
<title>Motor Upkeep Tracking Journal – Front Cover</title>
<link rel="stylesheet" href="https://fonts.googleapis.com/css2?family=Barlow+Condensed:wght@300;400&display=swap">
<style>
  :root {
    --backdrop: #f6e9e2;
    --cover-light: #40515f;
    --cover-mid: #344453;
    --cover-dark: #263240;
    --title-silver: #e4e2e0;
    --subtitle-silver: #cfcdcb;
  }
  * { margin: 0; padding: 0; box-sizing: border-box; }
  html, body {
    width: 1200px;
    height: 900px;
    overflow: hidden;
    background: var(--backdrop);
  }
  .canvas {
    width: 1200px;
    height: 900px;
    display: flex;
    align-items: center;
    justify-content: center;
  }
  .front-cover {
    width: 540px;
    height: 810px;
    background: linear-gradient(160deg, var(--cover-light) 0%, var(--cover-mid) 55%, var(--cover-dark) 100%);
    display: flex;
    flex-direction: column;
    align-items: center;
    padding-top: 215px;
    font-family: "Barlow Condensed", sans-serif;
  }
  .cover-title {
    color: var(--title-silver);
    font-weight: 300;
    font-size: 62px;
    letter-spacing: 0.5px;
    line-height: 1;
    white-space: nowrap;
  }
  .title-rule {
    width: 70px;
    height: 1px;
    background: var(--subtitle-silver);
    margin: 18px 0 14px;
  }
  .cover-subtitle {
    color: var(--subtitle-silver);
    font-weight: 400;
    font-size: 17px;
    letter-spacing: 5px;
    line-height: 1;
  }
</style>
</head>
<body>
  <main class="canvas">
    <section class="front-cover">
      <h1 class="cover-title">MOTOR UPKEEP</h1>
      <div class="title-rule"></div>
      <p class="cover-subtitle">TRACKING JOURNAL</p>
    </section>
  </main>
</body>
</html>
```